Travel Agency Website - Simple General

Need a 7 page simple design that is pretty repetitive. Need to be able to load quickly that is SEO optimized. Trying to give ideas on what they can do, be personal as we are local, but at the same time come across as professional and get information easily with little burden.

- Landing Page
- Brimwell Vacations Page
- Family Trips
- Road Trips from Texas
- Other Destinations
- About Us Page
- Contact Us Page

Target Market(s)

Families

Coding

Coded - Design and coding required

Number of Pages Required

5+ page

Colors

Designer to choose colors to be used in the design.

Requirements
Must have
• Like it to flow easily with our logo. Use that for colors, etc.

```html
<!DOCTYPE html>
<html lang="en">
<head>
<meta charset="utf-8">
<title>About Us – Lantern Road Travel Co.</title>
<link href="https://fonts.googleapis.com/css2?family=Poppins:wght@400;500;600;700&display=swap" rel="stylesheet">
<style>
:root{
  --teal:#0c4a5b;
  --teal-deep:#0b4658;
  --gold:#b8862f;
  --paper:#e4e4e1;
  --cream:#f6f2e6;
  --white:#ffffff;
}
*{margin:0;padding:0;box-sizing:border-box}
html,body{width:1019px;height:1200px;overflow:hidden;background:var(--white)}
body{position:relative;font-family:'Poppins',sans-serif;color:var(--teal)}
.abs{position:absolute}

.topbar{left:0;top:0;width:1019px;height:53px;background:linear-gradient(180deg,#e9e9e6,#dcdcd8)}
.topbar-phone{left:161px;top:17px;display:flex;align-items:center;gap:5px;font-weight:600;font-size:14px;color:var(--teal);letter-spacing:-.3px}
.brand-badge{left:476px;top:4px;width:66px;height:60px;border-radius:50%;background:var(--cream);display:flex;align-items:center;justify-content:center;text-align:center;font-size:8.5px;font-weight:600;line-height:1.15;color:var(--teal);z-index:3}
.top-social{top:20px;display:flex;gap:18px;left:806px}
.top-social span{width:15px;height:15px;border-radius:50%;border:1.5px solid var(--gold)}

.mainnav{left:0;top:53px;width:1019px;height:44px;background:var(--gold)}
.mainnav::before,.mainnav::after{content:"";position:absolute;left:0;right:0;border-top:1px dashed rgba(255,255,255,.8)}
.mainnav::before{top:6px}.mainnav::after{bottom:6px}
.mainnav ul{list-style:none;display:flex;justify-content:center;gap:27px;height:100%;align-items:center;padding-left:4px}
.mainnav li{font-size:9.2px;color:var(--white);text-transform:uppercase;letter-spacing:.1px}

.hero{left:0;top:97px;width:1019px;height:292px;background:linear-gradient(180deg,#8f8a84 0%,#b7a993 22%,#6a8d90 38%,#3f8a8f 55%,#9c8a7c 78%,#a38e7f 100%)}
.hero h1{position:absolute;left:0;right:0;top:92px;text-align:center;font-size:27px;font-weight:700;color:var(--white);letter-spacing:-.3px}
.hero-edge{left:0;top:340px;width:1019px;height:60px}

.gallery{left:111px;top:465px;display:flex;gap:7px}
.gallery div{width:127px;height:126px;border-radius:9px}

.portrait{left:166px;top:664px;width:303px;height:303px;border-radius:50%;background:linear-gradient(180deg,#e6ddcf 0%,#d8cfc2 45%,#8d8a86 65%,#5a6770 100%)}
.about-copy{left:512px;top:688px;width:345px}
.about-copy h2{font-size:28px;font-weight:700;letter-spacing:-.3px;line-height:34px;margin-bottom:12px}
.about-copy p{font-size:8.6px;line-height:13.3px;margin-bottom:13px;letter-spacing:-.05px;hyphens:auto;-webkit-hyphens:auto}

.footer-edge{left:0;top:1018px;width:1019px;height:50px}
.footer{left:0;top:1060px;width:1019px;height:140px;background:var(--teal-deep)}
.footer-badge{left:129px;top:1068px;width:120px;height:104px;border-radius:50%;background:var(--cream);display:flex;align-items:center;justify-content:center;text-align:center;font-size:12px;font-weight:600;line-height:1.2;color:var(--teal)}
.footer-contact{left:376px;top:1096px;display:flex;align-items:center;font-size:9px;color:var(--white)}
.footer-contact .item{display:flex;align-items:center;gap:5px}
.footer-contact .divider{width:1px;height:19px;background:rgba(255,255,255,.25);margin:0 23px 0 25px}
.footer-social{left:861px;top:1094px;display:flex;gap:5px}
.footer-social span{width:16px;height:16px;border-radius:50%;background:var(--gold)}
.footer-rule{left:366px;top:1128px;width:541px;height:1px;background:rgba(255,255,255,.18)}
.footer-legal{left:376px;top:1139px;width:531px;display:flex;justify-content:space-between;font-size:8.8px;color:var(--white)}
.footer-legal nav{display:flex;gap:7px}
</style>
</head>
<body>

<header>
  <div class="abs topbar"></div>
  <div class="abs topbar-phone">
    <svg width="14" height="14" viewBox="0 0 24 24"><path fill="#b8862f" d="M6.6 10.8a15.2 15.2 0 0 0 6.6 6.6l2.2-2.2a1 1 0 0 1 1-.25 11.4 11.4 0 0 0 3.6.57 1 1 0 0 1 1 1V20a1 1 0 0 1-1 1A17 17 0 0 1 3 4a1 1 0 0 1 1-1h3.5a1 1 0 0 1 1 1c0 1.25.2 2.45.57 3.57a1 1 0 0 1-.25 1z"/></svg>
    512.555.0148
  </div>
  <div class="abs brand-badge">Lantern Road<br>Travel Co.</div>
  <div class="abs top-social" aria-label="Social links"><span></span><span></span></div>
  <nav class="abs mainnav">
    <ul>
      <li>Home</li><li>Brimwell Vacations</li><li>Family Trips</li><li>Texas Road Trips</li><li>Other Destinations</li><li>About Us</li><li>Contact</li>
    </ul>
  </nav>
</header>

<section class="abs hero" role="img" aria-label="Beach at sunset with waves rolling onto the sand">
  <h1>About Our Family</h1>
</section>
<svg class="abs hero-edge" viewBox="0 0 1019 60" preserveAspectRatio="none">
  <path fill="#fff" d="M0 18 L30 20 L60 17 L95 22 L130 19 L170 24 L210 21 L245 27 L275 32 L300 28 L335 25 L360 20 L395 18 L430 22 L470 19 L505 23 L540 21 L575 25 L610 22 L650 27 L690 30 L720 26 L760 22 L800 25 L840 21 L880 18 L905 15 L930 17 L960 14 L990 16 L1019 12 L1019 60 L0 60Z"/>
</svg>

<section class="abs gallery" aria-label="Trip photo gallery">
  <div role="img" aria-label="Desert road through red rock canyon" style="background:linear-gradient(180deg,#a66a55,#6a5550 55%,#3a3a3c)"></div>
  <div role="img" aria-label="Hiker overlooking snowy mountains" style="background:linear-gradient(180deg,#3f7fc9,#c8d3dc 40%,#6b6e6a 75%,#4e5a45)"></div>
  <div role="img" aria-label="Calm beach at sunrise" style="background:linear-gradient(180deg,#e9c8a8,#f4dcc0 40%,#6cbfc2 60%,#f1d8c0)"></div>
  <div role="img" aria-label="Travelers walking with luggage down a city street" style="background:linear-gradient(180deg,#c9c6bf,#8f6f63 50%,#b9b3ad)"></div>
  <div role="img" aria-label="Family taking a selfie at the seaside" style="background:linear-gradient(180deg,#e2e6ea,#c39062 55%,#8a8c8e)"></div>
  <div role="img" aria-label="Backpack resting on a cliff above turquoise water" style="background:linear-gradient(180deg,#1fa6b3,#2e7c82 55%,#b86a3a)"></div>
</section>

<main>
  <div class="abs portrait" role="img" aria-label="Group of friends with arms around each other watching a cable car over the sea"></div>
  <article class="abs about-copy">
    <h2>About Our Family</h2>
    <p>We are a family-focused travel planning service dedicated to creating unforgettable experiences for families who love to explore the world together.</p>
    <p>Our journey started with a simple idea — to make travel easier, more personal, and completely stress-free for families. We understand how important it is to spend quality time with loved ones, and we believe every trip should become a lasting memory.</p>
    <p>We specialize in planning Brimwell vacations, road trips, family getaways, and destination experiences tailored to your needs, budget, and comfort.</p>
    <p>As a local and family-oriented business, we treat every client like part of our own family. From the first conversation to the final day of your trip, we are here to guide you every step of the way.</p>
  </article>
</main>

<svg class="abs footer-edge" viewBox="0 0 1019 50" preserveAspectRatio="none">
  <path fill="#0b4658" d="M0 26 L25 22 L55 24 L85 20 L115 17 L150 19 L185 15 L215 18 L250 13 L280 17 L310 14 L345 19 L380 22 L410 26 L440 22 L470 18 L500 20 L535 16 L570 19 L600 15 L635 18 L670 14 L705 17 L740 13 L775 16 L810 12 L840 15 L870 10 L900 6 L930 9 L960 12 L990 8 L1019 12 L1019 50 L0 50Z"/>
</svg>
<footer>
  <div class="abs footer"></div>
  <div class="abs footer-badge">Lantern Road<br>Travel Co.</div>
  <div class="abs footer-contact">
    <span class="item">
      <svg width="8" height="8" viewBox="0 0 24 24"><path fill="#fff" d="M6.6 10.8a15.2 15.2 0 0 0 6.6 6.6l2.2-2.2a1 1 0 0 1 1-.25 11.4 11.4 0 0 0 3.6.57 1 1 0 0 1 1 1V20a1 1 0 0 1-1 1A17 17 0 0 1 3 4a1 1 0 0 1 1-1h3.5a1 1 0 0 1 1 1c0 1.25.2 2.45.57 3.57a1 1 0 0 1-.25 1z"/></svg>
      512.555.0148
    </span>
    <span class="divider"></span>
    <span class="item">
      <svg width="8" height="7" viewBox="0 0 24 18"><path fill="#fff" d="M0 0h24v2L12 10 0 2zM0 4l12 8 12-8v14H0z"/></svg>
      hello@lanternroadtravel.com
    </span>
  </div>
  <div class="abs footer-social" aria-label="Social links"><span></span><span></span></div>
  <div class="abs footer-rule"></div>
  <div class="abs footer-legal">
    <span>2026 Lantern Road Travel Co. All Rights Reserved</span>
    <nav><span>Terms &amp;</span><span>|</span><span>Conditions</span><span>|</span><span>Privacy Policy</span></nav>
  </div>
</footer>

</body>
</html>
```